Design the Business card for NetVaultic

Business card required for a professional Cyber Security business.
Company Logo and Icon has already been provided however I would like other options for the logo and icon to compare to. Alternatively, please refine/enhance the image of the logo.icon I have already provided.

If you are going to use the provided logo and icon, I was thinking that the company raised Logo on White background would serve well on the front of the card. See attached. AND, a large company raised stand-alone icon to appear on black background on the back of the card with tagline 'Cyber Risk Management, Governance and Consulting' or 'Cyber Security for your Business' See attached.
Alternatively, provide your own design for the logo and icon.

Target Market(s)

Enterprise, Government, Financial.

Contact Information for Business Card

Tavin Orloweth
Founder and CEO

Email Address
Mobile Number
Website URL
LinkedIn URL

Logo Text

NetVaultic - see attached example of logo

Font styles to use
Other font styles liked:
• Berlin Sans FB

Requirements
Must have
• Clean large and bold icon on the back with tagline.
• Horizontal alignment,
Nice to have
• Round edges.
• Raised Logo/Icon
Should not have
• An unprofessional look and feel.

```html
<!DOCTYPE html>
<html lang="en">
<head>
<meta charset="utf-8">
<title>NetVaultic Business Card</title>
<link rel="stylesheet" href="https://fonts.googleapis.com/css2?family=Fredoka:wght@400;500&family=Roboto:wght@400&display=swap">
<style>
  :root {
    --backdrop: #2a2a2c;
    --card-white: #f2f2f2;
    --card-black: #18191b;
    --brand-blue: #1a73c4;
    --band-blue: #4472c4;
    --brand-yellow: #fcbd00;
    --text-grey: #4a4a4a;
  }
  html, body {
    margin: 0;
    width: 1200px;
    height: 960px;
    overflow: hidden;
    background: var(--backdrop);
  }
  .canvas { position: relative; width: 1200px; height: 960px; }
  .card {
    position: absolute;
    width: 600px;
    box-shadow: 0 4px 10px rgba(0,0,0,0.45);
    overflow: hidden;
  }
  .card-front { left: 314px; top: 113px; height: 343px; background: var(--card-white); }
  .card-back { left: 311px; top: 472px; height: 343px; background: var(--card-black); }

  .holder-name {
    position: absolute; left: 45px; top: 42px; margin: 0;
    font: 500 21px/1 "Fredoka", sans-serif; color: var(--brand-blue);
  }
  .holder-role {
    position: absolute; left: 45px; top: 67px; margin: 0;
    font: 400 14px/1 "Fredoka", sans-serif; color: var(--brand-yellow);
  }
  .contact-list {
    position: absolute; left: 45px; top: 97px; margin: 0; padding: 0; list-style: none;
    font: 400 14px/19.5px "Roboto", sans-serif; color: var(--text-grey);
  }
  .contact-list li { display: flex; align-items: center; gap: 6px; }
  .contact-icon { width: 14px; height: 14px; flex: none; }

  .decor-field {
    position: absolute; left: 240px; top: 68px; width: 380px; height: 300px;
    border-radius: 50% 0 0 0;
    background: radial-gradient(circle at 45% 45%, #4472c4 0%, #5b84cf 45%, #fcbd00 80%, rgba(252,189,0,0) 100%);
    opacity: 0.9;
  }

  .brand-lockup {
    position: absolute; left: 0; right: 0; top: 120px;
    display: flex; justify-content: center; align-items: center; gap: 14px;
  }
  .brand-dot { width: 64px; height: 64px; border-radius: 50%; background: var(--band-blue); }
  .brand-name { font: 500 48px/1 "Fredoka", sans-serif; color: var(--brand-blue); }

  .tagline-bands { position: absolute; left: 0; top: 271px; width: 600px; height: 33px; }
  .band {
    position: absolute; top: 0; height: 33px; width: 300px;
    display: flex; align-items: center; justify-content: center;
    font: 500 17px/1 "Fredoka", sans-serif; color: #ffffff;
  }
  .band-blue { left: 0; background: var(--band-blue); border-radius: 0 17px 17px 0; }
  .band-yellow { left: 300px; background: var(--brand-yellow); border-radius: 17px 0 0 17px; }
</style>
</head>
<body>
<div class="canvas">
  <section class="card card-front">
    <h1 class="holder-name">Tavin Orloweth</h1>
    <p class="holder-role">Founder &amp; CEO</p>
    <ul class="contact-list">
      <li>
        <svg class="contact-icon" viewBox="0 0 14 14"><rect x="3.5" y="0.5" width="7" height="13" rx="1.2" fill="none" stroke="#1a73c4" stroke-width="1.4"/><rect x="5" y="2.5" width="4" height="7" fill="#1a73c4"/></svg>
        555 014 2290
      </li>
      <li>
        <svg class="contact-icon" viewBox="0 0 14 14"><rect x="1" y="3" width="12" height="8" fill="#1a73c4"/><path d="M1 3 L7 8 L13 3" fill="none" stroke="#f2f2f2" stroke-width="1.2"/></svg>
        tavin@netvaultic.com
      </li>
      <li>
        <svg class="contact-icon" viewBox="0 0 14 14"><circle cx="7" cy="7" r="6" fill="#1a73c4"/><path d="M1 7 H13 M7 1 V13" stroke="#f2f2f2" stroke-width="1"/></svg>
        www.netvaultic.com
      </li>
      <li>
        <svg class="contact-icon" viewBox="0 0 14 14"><circle cx="7" cy="7" r="6" fill="#1a73c4"/></svg>
        netvaultic
      </li>
    </ul>
    <div class="decor-field" role="img" aria-label="Large decorative network-node brand symbol in blue and yellow"></div>
  </section>

  <section class="card card-back">
    <div class="brand-lockup">
      <span class="brand-dot"></span>
      <span class="brand-name">NetVaultic</span>
    </div>
    <div class="tagline-bands">
      <div class="band band-blue">Cyber Risk Management,</div>
      <div class="band band-yellow">Governance &amp; Consulting</div>
    </div>
  </section>
</div>
</body>
</html>
```